Create Packaging Designs for light bulb boxes (need asap)

Hi I want to have packaging designed in a simple way for our new light bulb order that is on the way. I need this done very quickly. I am looking for a nice, simple design and for it to be print ready for the packaging company in China.
I would like and ash black/very dark grey box colour and for the writing to be in gold (per the logo).
Once the winner is chosen I will then need you to change some of the text for relevant information (like bulb specification).
Our website is www.harrowmeta.com.au
Packaging sizes are as follows:
(Sizes are in mm)
G125: L130W190H130
G95: L100W100H145
T45: L48W48H120
T30*300: L35W35H310
A80: L92W92H162
ST64: L70W70H145
ST45: L52W52H93
T30*225: L33W33H235
G80: L85W85H130

```html
<!DOCTYPE html>
<html lang="en">
<head>
<meta charset="utf-8">
<title>Harrow Meta – Bulb Box Packaging Panels</title>
<link rel="stylesheet" href="https://fonts.googleapis.com/css2?family=Josefin+Sans:wght@400&family=Courier+Prime&display=swap">
<style>
  :root {
    --canvas: #f3f3f1;
    --box-ash: #2b2b2a;
    --box-edge: #1a1a19;
    --gold: #b59a6e;
    --fold: #3a3a38;
  }
  * { box-sizing: border-box; margin: 0; padding: 0; }
  html, body { width: 1200px; height: 844px; overflow: hidden; background: var(--canvas); }
  .sheet { position: relative; width: 1200px; height: 844px; }

  .panel {
    position: absolute;
    background: var(--box-ash);
    border: 1px solid var(--box-edge);
    color: var(--gold);
  }
  .panel--top   { left: 100px; top: 70px;  width: 250px; height: 250px; }
  .panel--front { left: 100px; top: 320px; width: 250px; height: 420px; }
  .panel--spec  { left: 350px; top: 320px; width: 250px; height: 420px; }
  .panel--cert  { left: 600px; top: 320px; width: 250px; height: 420px; }
  .panel--back  { left: 850px; top: 320px; width: 250px; height: 420px; }
  .panel--front, .panel--cert, .panel--back { border-right-color: var(--fold); }

  .brand {
    position: absolute; left: 0; right: 0;
    display: flex; flex-direction: column; align-items: center; gap: 26px;
    font-family: "Josefin Sans", sans-serif; font-weight: 400;
    color: var(--gold); text-transform: uppercase;
  }
  .brand__mark {
    width: 74px; height: 74px; border: 4px solid var(--gold); border-radius: 50%;
  }
  .brand__name { font-size: 30px; letter-spacing: 3px; line-height: 1; text-align: center; }
  .panel--front .brand, .panel--cert .brand, .panel--back .brand { top: 110px; }
  .panel--top .brand { top: 70px; gap: 20px; }
  .panel--top .brand__mark { width: 60px; height: 60px; }
  .panel--top .brand__name { font-size: 20px; }

  .spec-list {
    position: absolute; left: 20px; bottom: 30px;
    list-style: none;
    font-family: "Courier Prime", monospace; font-size: 14px; line-height: 1.7;
  }
  .spec-list li::before { content: "- "; }

  .sticker-area {
    position: absolute; right: 18px; bottom: 120px;
    width: 70px; height: 70px;
    border: 1.5px solid #111;
    display: flex; align-items: center; justify-content: center;
    font-family: "Courier Prime", monospace; font-size: 11px; color: var(--gold);
  }

  .cert-code {
    position: absolute; left: 18px; bottom: 110px;
    font-family: "Courier Prime", monospace; font-size: 13px;
  }
</style>
</head>
<body>
<main class="sheet">
  <section class="panel panel--top" aria-label="Lid">
    <div class="brand">
      <span class="brand__mark"></span>
      <span class="brand__name">Harrow Meta</span>
    </div>
  </section>

  <section class="panel panel--front" aria-label="Front face">
    <div class="brand">
      <span class="brand__mark"></span>
      <span class="brand__name">Harrow<br>Meta</span>
    </div>
  </section>

  <section class="panel panel--spec" aria-label="Specification face">
    <ul class="spec-list">
      <li>2 year warranty</li>
      <li>15.000 h</li>
      <li>LED</li>
      <li>SAA TEST</li>
    </ul>
    <div class="sticker-area">STICKER</div>
  </section>

  <section class="panel panel--cert" aria-label="Approval face">
    <div class="brand">
      <span class="brand__mark"></span>
      <span class="brand__name">Harrow<br>Meta</span>
    </div>
    <p class="cert-code">saa 40862</p>
  </section>

  <section class="panel panel--back" aria-label="Back face">
    <div class="brand">
      <span class="brand__mark"></span>
      <span class="brand__name">Harrow<br>Meta</span>
    </div>
  </section>
</main>
</body>
</html>
```